KR Appraisals website redesign

I would like to refresh my existing website of www.krappraisals-example.com with new graphics, look and feel, as well as updated structure and wording. Content and layout changes have been uploaded to this project Brief.

My existing website has a dark feel. I am now looking for a light and energetic feel. Financial Services is my industry, so the website should be reflect that. I would also like to reflect the concepts of Trust, Service and Expertise.

The website must be serious and upmarket.

Target Market(s)

Corporate board members, CFO's, treasurers and controllers
Auditors, tax advisors, private equity and venture capital asset managers, investors, tax authorities

Industry/Entity Type

Financial Service

Coding

Coded - Design and coding required

Number of Pages Required

5+ page

Font styles to use
Sans Serif
Other font styles liked:
• Designer can choose another modern font

Colors
0355a3
3277b5
85acd3
eaf1f7
f37122
f68d4d
9bcb3c
acd037
cadf82

Requirements
Must have
• Good hi resolution pictures that convey "Finance", "Trust", "Service" or "Expertise".
• An anti-bot (such as Captcha) mechanism in the contact form.
Should not have
• Must not have all content on one rolling screen.

```html
<!DOCTYPE html>
<html lang="en">
<head>
<meta charset="utf-8">
<title>About Us – KR Appraisals</title>
<link rel="stylesheet" href="https://fonts.googleapis.com/css2?family=Montserrat:wght@500;600;700&family=Mulish:wght@400;500&display=swap">
<style>
:root{
  --blue:#0355a3;
  --orange:#f37122;
  --green:#9bcb3c;
  --text:#666666;
  --nav:#777777;
  --dark:#333333;
  --footer-text:#9a9a9a;
  --white:#ffffff;
  --rule:#5a5a5a;
}
*{margin:0;padding:0;box-sizing:border-box}
html,body{width:1200px;height:1159px;overflow:hidden;background:var(--white)}
body{font-family:"Mulish",sans-serif;color:var(--text);position:relative}
.site-header{position:absolute;left:0;top:0;width:1200px;height:100px;
  background:linear-gradient(90deg,#dfe0d6 0%,#ebebdf 35%,#f3f3e2 70%,#f7f7e6 100%)}
.brand{position:absolute;left:161px;top:34px;display:flex;align-items:center;gap:10px;
  font-family:"Montserrat",sans-serif;font-weight:500;font-size:22px;color:#7a7a7a}
.brand-mark{width:22px;height:22px;border:2px solid #7a7a7a}
.main-nav{position:absolute;top:45px;left:0;width:1200px}
.main-nav a{position:absolute;font-family:"Montserrat",sans-serif;font-weight:600;font-size:11.5px;
  color:var(--nav);text-decoration:none;letter-spacing:.1px}
.main-nav a.current{color:var(--blue)}
.page-title{position:absolute;top:183px;width:1200px;text-align:center;font-family:"Montserrat",sans-serif;
  font-weight:700;font-size:39px;color:var(--orange);letter-spacing:-.5px}
.intro{position:absolute;left:300px;width:618px;text-align:center;font-size:12px;line-height:19.5px}
.pillars-line{position:absolute;top:424px;width:1200px;text-align:center;font-size:15px;color:var(--text)}
.t-blue{color:var(--blue)} .t-orange{color:var(--orange)} .t-green{color:var(--green)}
.pillars-graphic{position:absolute;left:0;top:470px}
.pillar-text{position:absolute;top:588px;width:270px;text-align:center;font-size:12px;line-height:19.5px}
.pillar-text b{font-weight:500}
.site-footer{position:absolute;left:0;top:0;width:1200px;height:1159px;pointer-events:none}
.footer-brand{position:absolute;top:862px;width:1200px;display:flex;justify-content:center;align-items:center;gap:10px;
  font-family:"Montserrat",sans-serif;font-weight:500;font-size:22px;color:#8a8a8a}
.footer-brand .brand-mark{border-color:#8a8a8a}
.footer-rule{position:absolute;left:161px;width:878px;height:1px;background:var(--rule)}
.footer-nav{position:absolute;top:966px;width:1200px;display:flex;justify-content:center;gap:41px}
.footer-nav a{font-family:"Montserrat",sans-serif;font-weight:600;font-size:11.5px;color:#8c8c8c;text-decoration:none}
.footer-nav a.current{color:var(--green)}
.footer-col{position:absolute;top:1022px;font-size:11px;line-height:22.5px;color:var(--footer-text)}
.footer-col h3{font-family:"Montserrat",sans-serif;font-weight:600;font-size:13.5px;color:var(--orange);margin-bottom:9px;line-height:18px}
.footer-col .hl-green{color:var(--green)} .footer-col .hl-white{color:var(--white)}
.address{display:flex;gap:10px;line-height:16.5px;margin-top:3px}
.phone{display:flex;gap:10px;align-items:center;margin-top:15px;color:var(--white);font-size:11.5px}
.badge{position:absolute;background:#4a4a4a;border-radius:6px}
</style>
</head>
<body>
<header class="site-header">
  <div class="brand"><span class="brand-mark"></span>KR Appraisals</div>
  <nav class="main-nav">
    <a style="left:611px" href="#">HOME</a>
    <a class="current" style="left:686px" href="#">ABOUT</a>
    <a style="left:766px" href="#">SERVICES</a>
    <a style="left:861px" href="#">NEWS &amp; VIEWS</a>
    <a style="left:985px" href="#">CONTACT</a>
  </nav>
</header>

<main>
  <h1 class="page-title">ABOUT US</h1>
  <p class="intro" style="top:270px">KR Appraisals, founded in 2012, is a boutique corporate finance practice servicing companies throughout Europe and North America. Our office is located in the Netherlands in the Harbourside Science Park. Our clients come from a broad range of industries with valuations ranging between micro-cap and large-cap.</p>
  <p class="intro" style="top:348px">KR Appraisals assists companies with valuations of businesses and intellectual property, M&amp;A advisory, business plan coaching and purchase price allocation (PPA). Through our bespoke approach and global network, we customize teams to the needs of our clients.</p>
  <p class="pillars-line"><span class="t-blue">Trust</span>, <span class="t-orange">Service</span> and <span class="t-green">Expertise</span> are the 3 pillars of KR Appraisals.</p>

  <svg class="pillars-graphic" width="1200" height="110" viewBox="0 0 1200 110" aria-hidden="true">
    <line x1="345" y1="53" x2="448" y2="53" stroke="#0355a3" stroke-width="1.5"/>
    <line x1="448" y1="53" x2="550" y2="53" stroke="#f37122" stroke-width="1.5"/>
    <line x1="650" y1="53" x2="752" y2="53" stroke="#f37122" stroke-width="1.5"/>
    <line x1="752" y1="53" x2="853" y2="53" stroke="#9bcb3c" stroke-width="1.5"/>
    <circle cx="295" cy="53" r="51" fill="#0355a3"/>
    <circle cx="600" cy="53" r="51" fill="#f37122"/>
    <circle cx="902" cy="53" r="51" fill="#9bcb3c"/>
    <g font-family="Montserrat, sans-serif" font-weight="600" font-size="15" fill="#fff" text-anchor="middle">
      <text x="295" y="59">TRUST</text>
      <text x="599" y="59">SERVICES</text>
      <text x="902" y="59">EXPERTISE</text>
    </g>
  </svg>

  <p class="pillar-text" style="left:161px"><b class="t-blue">Trust</b> is paramount. Clients rely on KR Appraisals for confidentiality, transparency and independence.</p>
  <p class="pillar-text" style="left:465px"><b class="t-orange">Service</b> is front and center at KR Appraisals. We consider the needs of all stakeholders and the personal needs of the client team involved.</p>
  <p class="pillar-text" style="left:769px"><b class="t-green">Expertise</b> is core to the philosophy of KR Appraisals. Our global network of professionals maintain and continue to develop the knowledge and experience that you expect from your trusted corporate finance partner.</p>
</main>

<footer>
  <svg style="position:absolute;left:0;top:0" width="1200" height="1159" aria-hidden="true">
    <polygon points="0,874 600,806 1200,874 1200,1159 0,1159" fill="#333333"/>
  </svg>
  <div class="footer-brand"><span class="brand-mark"></span>KR Appraisals</div>
  <div class="footer-rule" style="top:951px"></div>
  <nav class="footer-nav">
    <a class="current" href="#">HOME</a><a href="#">ABOUT</a><a href="#">SERVICES</a><a href="#">NEWS &amp; VIEWS</a><a href="#">CONTACT</a>
  </nav>
  <div class="footer-rule" style="top:996px"></div>

  <div class="footer-col" style="left:163px">
    <h3>CREDITS</h3>
    <div>© 2019 <span class="hl-green">KR Appraisals</span></div>
    <div>Logo by <span class="hl-white">Mara Lindqvist</span></div>
    <div>Website by <span class="hl-green">Brightline Studio</span></div>
  </div>

  <div class="footer-col" style="left:390px">
    <h3>LEIDEN</h3>
    <div class="address">
      <svg width="9" height="13" viewBox="0 0 9 13"><path d="M4.5 0A4.5 4.5 0 0 0 0 4.5C0 8 4.5 13 4.5 13S9 8 9 4.5A4.5 4.5 0 0 0 4.5 0Zm0 6.3a1.8 1.8 0 1 1 0-3.6 1.8 1.8 0 0 1 0 3.6Z" fill="#9bcb3c"/></svg>
      <div>Kanaalweg 48<br>2311 AB Leiden</div>
    </div>
    <div class="phone">
      <svg width="12" height="12" viewBox="0 0 24 24"><path d="M6.6 10.8a15.1 15.1 0 0 0 6.6 6.6l2.2-2.2c.3-.3.7-.4 1-.2 1.1.4 2.3.6 3.6.6.6 0 1 .4 1 1V20c0 .6-.4 1-1 1A17 17 0 0 1 3 4c0-.6.4-1 1-1h3.5c.6 0 1 .4 1 1 0 1.3.2 2.5.6 3.6.1.3 0 .7-.2 1Z" fill="#9bcb3c"/></svg>
      070 555 0142
    </div>
  </div>

  <div class="footer-col" style="left:617px">
    <h3>AMSTERDAM</h3>
    <div class="address">
      <svg width="9" height="13" viewBox="0 0 9 13"><path d="M4.5 0A4.5 4.5 0 0 0 0 4.5C0 8 4.5 13 4.5 13S9 8 9 4.5A4.5 4.5 0 0 0 4.5 0Zm0 6.3a1.8 1.8 0 1 1 0-3.6 1.8 1.8 0 0 1 0 3.6Z" fill="#9bcb3c"/></svg>
      <div>Zuidplein 14<br>1077 XV Amsterdam</div>
    </div>
    <div class="phone">
      <svg width="12" height="12" viewBox="0 0 24 24"><path d="M6.6 10.8a15.1 15.1 0 0 0 6.6 6.6l2.2-2.2c.3-.3.7-.4 1-.2 1.1.4 2.3.6 3.6.6.6 0 1 .4 1 1V20c0 .6-.4 1-1 1A17 17 0 0 1 3 4c0-.6.4-1 1-1h3.5c.6 0 1 .4 1 1 0 1.3.2 2.5.6 3.6.1.3 0 .7-.2 1Z" fill="#9bcb3c"/></svg>
      020 555 0178
    </div>
  </div>

  <div class="badge" role="img" aria-label="Professional membership badge" style="left:856px;top:1015px;width:170px;height:40px"></div>
  <div class="badge" role="img" aria-label="Professional society accreditation badge" style="left:854px;top:1063px;width:170px;height:70px"></div>
</footer>
</body>
</html>
```